Veldmark Supplies Business Card

Professional business card that stand out to our potential customers. Front and back with clean modern design

Industry/Entity Type

Oil and gas

Contact Information for Business Card

Name, address, website , office phone and cell number

Requirements
Must have
• Editable files for each employee

```html
<!DOCTYPE html>
<html lang="en">
<head>
<meta charset="utf-8">
<title>Veldmark Supplies Business Card</title>
<link rel="stylesheet" href="https://fonts.googleapis.com/css2?family=Roboto:wght@400;700;900&display=swap">
<style>
  :root {
    --stage: #2a2a2c;
    --card-dark: #1d1d1f;
    --emboss: #3b3b3e;
    --brand-red: #e21b24;
    --brand-blue: #2bb3d6;
    --ink-white: #ffffff;
    --ink-dark: #1d1d1f;
  }
  * { margin: 0; padding: 0; box-sizing: border-box; }
  html, body { width: 1200px; height: 852px; overflow: hidden; }
  body {
    background: var(--stage);
    font-family: "Roboto", Arial, sans-serif;
    position: relative;
  }
  .card {
    position: absolute;
    top: 281px;
    width: 500px;
    height: 290px;
    border-radius: 18px;
    overflow: hidden;
    background: var(--card-dark);
  }
  .card-back { left: 70px; }
  .card-front { left: 630px; }

  .back-brand {
    position: absolute; inset: 0;
    display: flex; flex-direction: column; align-items: center; justify-content: center; gap: 18px;
  }
  .back-mark { width: 54px; height: 54px; background: var(--emboss); }
  .back-name {
    font-weight: 900; font-size: 26px; letter-spacing: 2px; text-transform: uppercase;
    color: var(--emboss);
  }

  .front-bands { position: absolute; inset: 0; width: 500px; height: 290px; }
  .front-brand {
    position: absolute; left: 24px; top: 48px;
    font-weight: 900; font-size: 20px; letter-spacing: 1px; text-transform: uppercase;
    color: var(--brand-blue);
  }
  .front-mark {
    position: absolute; left: 370px; top: 150px; width: 100px; height: 100px;
    background: var(--ink-dark);
  }
  .person { position: absolute; left: 24px; top: 110px; color: var(--ink-white); }
  .person-name { font-weight: 700; font-size: 18px; }
  .person-role { font-size: 11px; margin-top: 3px; }
  .contacts {
    position: absolute; left: 24px; top: 190px; list-style: none;
    color: var(--ink-white); font-size: 11px;
  }
  .contacts li { display: flex; align-items: center; gap: 8px; height: 17px; }
  .contacts svg { width: 11px; height: 11px; fill: var(--ink-white); }
  .address {
    position: absolute; left: 24px; top: 262px;
    color: var(--ink-white); font-size: 11px;
  }
</style>
</head>
<body>
  <section class="card card-back" aria-label="Card back">
    <div class="back-brand">
      <div class="back-mark"></div>
      <div class="back-name">Veldmark Supplies</div>
    </div>
  </section>

  <section class="card card-front" aria-label="Card front">
    <svg class="front-bands" viewBox="0 0 500 290" aria-hidden="true">
      <rect width="500" height="290" fill="var(--card-dark)"/>
      <rect x="0" y="98" width="340" height="67" fill="var(--brand-blue)"/>
      <polygon points="420,0 500,0 500,95" fill="var(--brand-blue)"/>
      <polygon points="0,165 340,165 340,118 500,118 500,290 0,290" fill="var(--brand-red)"/>
    </svg>
    <div class="front-brand">Veldmark Supplies</div>
    <div class="front-mark"></div>
    <div class="person">
      <div class="person-name">Alex Rowan Hale</div>
      <div class="person-role">Managing Director</div>
    </div>
    <ul class="contacts">
      <li><svg viewBox="0 0 12 12"><path d="M2 1h3l1 3-1.5 1a7 7 0 0 0 3 3L9 6.5l3 1v3A1.5 1.5 0 0 1 10.5 12 10.5 10.5 0 0 1 0 1.5 1.5 1.5 0 0 1 2 1z"/></svg>(555)010-0142</li>
      <li><svg viewBox="0 0 12 12"><path d="M0 2h12v8H0z M1 3l5 4 5-4" fill="none" stroke="#fff" stroke-width="1.2"/></svg>sales@veldmarksupplies.com</li>
      <li><svg viewBox="0 0 12 12"><circle cx="6" cy="6" r="5" fill="none" stroke="#fff" stroke-width="1.2"/><path d="M1 6h10M6 1c-3 3-3 7 0 10M6 1c3 3 3 7 0 10" fill="none" stroke="#fff" stroke-width="1"/></svg>www.veldmarksupplies.com</li>
    </ul>
    <div class="address">420 Brandt Lane Suite 5 Midvale, Tx 79000</div>
  </section>
</body>
</html>
```